Poloshirt Packaging

We need a very attractive packaging design for our poloshirts. We are wholesaler of the schoolwear market. See what we currently have. I dont want any specific sizing put on the packaging. One design for all poloshirts (2 sides).
our logo is attached aswell

Target Market(s)

Parents

Requirements
Must have
• Our logo
Should not have
• size or age

```html
<!DOCTYPE html>
<html lang="en">
<head>
<meta charset="utf-8">
<title>Brightwell Poloshirt Packaging</title>
<link rel="stylesheet" href="https://fonts.googleapis.com/css2?family=Mulish:wght@700;800&family=Arimo:wght@400;700&display=swap">
<style>
  :root {
    --navy: #0d2f5a;
    --red: #d92e2e;
    --wave-red: #e3402a;
    --wave-orange: #ef8a1f;
    --wave-yellow: #f5c518;
    --gold-light: #f2b73a;
    --gold-dark: #e6a224;
    --ink: #1c1c1c;
    --white: #ffffff;
    --shadow: #b9b9b9;
  }
  html, body {
    margin: 0;
    padding: 0;
    width: 1200px;
    height: 852px;
    overflow: hidden;
    background: var(--white);
  }
  .artboard {
    position: relative;
    width: 1100px;
    height: 781px;
    transform: scale(1.0909);
    transform-origin: 0 0;
    font-family: "Mulish", sans-serif;
  }
  .shapes {
    position: absolute;
    inset: 0;
  }
  .brand-name {
    position: absolute;
    margin: 0;
    color: var(--navy);
    font-family: "Mulish", sans-serif;
    font-weight: 700;
    line-height: 1;
    white-space: nowrap;
  }
  .product-name {
    position: absolute;
    margin: 0;
    color: var(--red);
    font-family: "Mulish", sans-serif;
    font-weight: 800;
    line-height: 1;
    white-space: nowrap;
  }
  .front .brand-name { left: 60px; top: 484px; font-size: 76px; }
  .front .product-name { left: 62px; top: 572px; font-size: 33px; }
  .back .brand-name { left: 648px; top: 232px; font-size: 60px; }
  .back .product-name { left: 710px; top: 354px; font-size: 30px; }
  .features {
    position: absolute;
    left: 62px;
    top: 623px;
    margin: 0;
    padding: 2px 6px;
    background: var(--navy);
    color: var(--white);
    font-family: "Arimo", sans-serif;
    font-size: 11px;
    line-height: 13px;
    white-space: nowrap;
  }
  .safety-note {
    position: absolute;
    left: 668px;
    top: 713px;
    width: 216px;
    height: 40px;
    box-sizing: border-box;
    border: 1px solid var(--ink);
    margin: 0;
    padding: 3px 4px;
    font-family: "Arimo", sans-serif;
    font-size: 8.5px;
    line-height: 10px;
    text-align: center;
    color: var(--ink);
  }
  .safety-note strong { display: block; text-decoration: underline; font-size: 9px; }
</style>
</head>
<body>
<div class="artboard">
  <svg class="shapes" viewBox="0 0 1100 781" width="1100" height="781">
    <defs>
      <linearGradient id="shirt-gold" x1="0" y1="0" x2="0" y2="1">
        <stop offset="0" stop-color="var(--gold-light)"/>
        <stop offset="1" stop-color="var(--gold-dark)"/>
      </linearGradient>
      <linearGradient id="front-wave" x1="0" y1="0" x2="1" y2="0">
        <stop offset="0" stop-color="var(--wave-red)"/>
        <stop offset="0.5" stop-color="var(--wave-orange)"/>
        <stop offset="1" stop-color="var(--wave-yellow)"/>
      </linearGradient>
      <linearGradient id="back-wave" x1="0" y1="0" x2="1" y2="0">
        <stop offset="0" stop-color="var(--wave-yellow)"/>
        <stop offset="0.5" stop-color="var(--wave-orange)"/>
        <stop offset="1" stop-color="var(--wave-red)"/>
      </linearGradient>
    </defs>

    <rect class="panel-shadow" x="19" y="23" width="526" height="742" fill="var(--shadow)"/>
    <rect class="front-shirt" x="14" y="18" width="526" height="742" fill="url(#shirt-gold)" stroke="#555" stroke-width="0.6" role="img" aria-label="Photo of a folded gold school poloshirt in a clear bag, front view"/>
    <path class="front-wave" d="M14,380 C120,335 220,325 300,262 C380,200 460,150 540,172 L540,235 C460,222 400,262 330,322 C250,392 150,412 14,466 Z" fill="url(#front-wave)"/>
    <path class="front-swoosh" d="M325,760 C395,718 450,640 540,640 L540,700 C490,700 462,730 440,760 Z" fill="var(--red)"/>

    <rect class="panel-shadow" x="546" y="23" width="526" height="742" fill="var(--shadow)"/>
    <rect class="back-shirt" x="541" y="18" width="526" height="742" fill="url(#shirt-gold)" stroke="#555" stroke-width="0.6" role="img" aria-label="Photo of a folded gold school poloshirt in a clear bag, back view"/>
    <path class="back-wave" d="M541,393 C650,398 720,460 820,450 C920,440 980,398 1067,404 L1067,470 C980,462 920,520 820,526 C720,532 650,472 541,452 Z" fill="url(#back-wave)"/>
    <path class="back-swoosh" d="M905,760 C932,700 985,652 1067,662 L1067,705 C1012,700 982,728 962,760 Z" fill="var(--red)"/>

    <g class="recycle-mark" fill="none" stroke="var(--ink)" stroke-width="2">
      <path d="M940,722 L956,748 L924,748 Z"/>
      <text x="940" y="744" font-family="Arimo, sans-serif" font-size="10" text-anchor="middle" fill="var(--ink)" stroke="none">5</text>
      <text x="940" y="757" font-family="Arimo, sans-serif" font-size="6" text-anchor="middle" fill="var(--ink)" stroke="none">PP</text>
    </g>
  </svg>

  <section class="front">
    <h1 class="brand-name">Brightwell</h1>
    <p class="product-name">POLOSHIRT</p>
    <p class="features">Superior weight fabric &nbsp;|&nbsp; Easy Care - Low iron &nbsp;|&nbsp; Reactive Dyes</p>
  </section>

  <section class="back">
    <h2 class="brand-name">Brightwell</h2>
    <p class="product-name">POLOSHIRT</p>
    <p class="safety-note"><strong>SAFETY FIRST</strong>TO AVOID DANGER OF SUFFOCATION KEEP THIS WRAPPER AWAY FROM BABIES AND CHILDREN</p>
  </section>
</div>
</body>
</html>
```